Construction business card

I need a new business card, they can connect with my logo, brand.
What we do is residential house , design and build
I like: Navy blue / black
I attached our logo, brand,
and, some idea for business card.

```html
<!DOCTYPE html>
<html lang="en">
<head>
<meta charset="utf-8">
<title>Ridgeway Building Group – Business Card</title>
<link href="https://fonts.googleapis.com/css2?family=Arimo:wght@400;700&family=Quicksand:wght@500&display=swap" rel="stylesheet">
<style>
  :root {
    --page-bg: #c9e6e8;
    --card-dark: #03030c;
    --card-navy: #07072e;
    --brand-blue: #3f86d4;
    --text-light: #e6e8ee;
    --plan-tone-a: #15151f;
    --plan-tone-b: #0a0a14;
  }
  * { margin: 0; padding: 0; box-sizing: border-box; }
  html, body {
    width: 1200px; height: 1200px; overflow: hidden;
    background: var(--page-bg);
  }
  .canvas {
    width: 1200px; height: 1200px;
    display: flex; flex-direction: column; align-items: center; justify-content: center;
    gap: 44px;
  }
  .card {
    position: relative;
    width: 880px; height: 503px;
    background: linear-gradient(100deg, var(--card-dark) 0%, var(--card-navy) 100%);
    overflow: hidden;
    font-family: "Arimo", Arial, sans-serif;
  }
  .plan-area {
    position: absolute;
    left: 0; bottom: 0;
    width: 420px; height: 190px;
    background: linear-gradient(160deg, var(--plan-tone-a) 0%, var(--plan-tone-b) 100%);
    opacity: 0.8;
    clip-path: polygon(0 25%, 70% 0, 100% 100%, 0 100%);
  }
  .brand-mark {
    display: flex; align-items: center; gap: 14px;
    color: #ffffff;
    font-family: "Arimo", Arial, sans-serif;
    font-weight: 700;
    line-height: 1.05;
    position: relative;
  }
  .brand-mark .brand-square {
    width: 26px; height: 26px; background: var(--brand-blue); flex: none;
  }
  .brand-mark .brand-name { font-size: 34px; letter-spacing: 0.5px; }

  /* Front side */
  .card--front .brand-mark { position: absolute; left: 90px; top: 190px; }
  .contact {
    position: absolute; left: 500px; top: 150px;
    color: var(--text-light);
  }
  .contact-name {
    font-family: "Quicksand", Arial, sans-serif;
    font-weight: 500;
    font-size: 44px;
    color: var(--brand-blue);
    line-height: 1;
  }
  .contact-role { font-size: 17px; margin-top: 2px; margin-bottom: 34px; }
  .contact-list { list-style: none; font-size: 21px; }
  .contact-list li { display: flex; align-items: flex-start; gap: 22px; margin-bottom: 10px; line-height: 1.3; }
  .contact-list li.address { margin-bottom: 18px; }
  .contact-list svg { width: 22px; height: 22px; flex: none; margin-top: 2px; }

  /* Back side */
  .card--back .brand-mark {
    position: absolute; left: 50%; top: 44%; transform: translate(-50%, -50%);
  }
  .card--back .brand-name { font-size: 44px; }
  .card--back .brand-square { width: 34px; height: 34px; }
</style>
</head>
<body>
<main class="canvas">

  <section class="card card--front" aria-label="Business card, contact side">
    <div class="plan-area" role="img" aria-label="Faint architectural floor plan in the background"></div>
    <div class="brand-mark">
      <span class="brand-square"></span>
      <span class="brand-name">Ridgeway<br>Building Group</span>
    </div>
    <div class="contact">
      <p class="contact-name">Sam Carter</p>
      <p class="contact-role">Manager</p>
      <ul class="contact-list">
        <li class="address">
          <svg viewBox="0 0 24 24" aria-hidden="true"><circle cx="12" cy="10" r="8" fill="none" stroke="#3f86d4" stroke-width="3"/><circle cx="12" cy="10" r="2.5" fill="#3f86d4"/></svg>
          <span>48 Harbour Lane,<br>Westmere, Vic 3190</span>
        </li>
        <li>
          <svg viewBox="0 0 24 24" aria-hidden="true"><path d="M6 2l4 4-2.5 2.5a12 12 0 0 0 8 8L18 14l4 4-3 3C10 21 3 14 3 5z" fill="#3f86d4"/></svg>
          <span>0400 555 017</span>
        </li>
        <li>
          <svg viewBox="0 0 24 24" aria-hidden="true"><rect x="2" y="5" width="20" height="14" fill="none" stroke="#3f86d4" stroke-width="2"/><path d="M2 5l10 8 10-8M2 19l8-7M22 19l-8-7" fill="none" stroke="#3f86d4" stroke-width="2"/></svg>
          <span>info@ridgewaybuilding.com.au</span>
        </li>
        <li>
          <svg viewBox="0 0 24 24" aria-hidden="true"><circle cx="12" cy="12" r="10" fill="#3f86d4"/><path d="M2 12h20M12 2v20M5 6h14M5 18h14" stroke="#07072e" stroke-width="1.4"/><ellipse cx="12" cy="12" rx="4.5" ry="10" fill="none" stroke="#07072e" stroke-width="1.4"/></svg>
          <span>www.ridgewaybuilding.com.au</span>
        </li>
      </ul>
    </div>
  </section>

  <section class="card card--back" aria-label="Business card, brand side">
    <div class="plan-area" role="img" aria-label="Faint architectural floor plan in the background"></div>
    <div class="brand-mark">
      <span class="brand-square"></span>
      <span class="brand-name">Ridgeway<br>Building Group</span>
    </div>
  </section>

</main>
</body>
</html>
```